BRAMBLEFORD CONSTRUCTIONS B-Card

I currently have a b-card design but will be removing the image (tree) from the logo and have text only.
I want the card to be classy and strong within the building and construction industry.
I will be using Spot UV on the cards as per the attached examples. I will also send through some sketched ideas that I have in mind.
The color blue is similar to the image (No. 6) attached images

Target Market(s)

middle to maturre aged.
Home Owners / Renovators and Builders

Industry/Entity Type

Construction

Contact Information for Business Card

BRAMBLEFORD CONSTRUCTIONS
Name: Gareth Pennick
Title: Project Manager
Mobile: 0427 351 804
Office: (08) 9316 5172
Address: 47C Corvell Street, Malaga WA 6090
Email: info@bramblefordhomes.com.au
PO Box: 3817 Malaga WA 6944

Colors
0592cd
33a6d7
85cae6
1b1b1b

Requirements
Must have
• 1. It must have spot UV on the front of card, maybe back of card too
• 2. I really like the blue on image 6. (or at least a really cool electric blue against the charcoal grey background)
• 3. The font must be slimline and modern. Easy to read
• 4. There must be no black used on the card... Only greys and dark charcoal greys
• 5. Use only the text from the logo "Brambleford Constructions" Not the image of the tree. I am wanting the b-cards to be more masculine.
Nice to have
• 1. I like the design concept on image 6. but happy to see what else you can do with the Spot UV
• 2. Unless you have a really cool idea of the image of the tree (from previous logo) Spot UV somewhere in the design concept thats original and different then I am keen to see what you come up with
• 3. Try changing the color of the logo eg. full white or Blue and white
• 4. Another option is to have the Brambleford Logo on the front of card with the spot UV in the background of text which we specialise in eg, Roofing, Ceiling, Insulation, Gutter Guards, Electrical, Insurance etc and we can add or reduce items as required. Similar to image 12.
Should not have
• Do not include the image of the tree from previous logo. unless you have a really cool idea of Spot UV somewhere in the design concept thats original and different.

```html
<!DOCTYPE html>
<html lang="en">
<head>
<meta charset="utf-8">
<title>Brambleford Constructions Business Card</title>
<link href="https://fonts.googleapis.com/css2?family=Open+Sans:wght@400;600&display=swap" rel="stylesheet">
<style>
  :root {
    --backdrop: #e8e6e3;
    --card-blue: #2eaae2;
    --card-charcoal: #262626;
    --uv-charcoal: #353535;
    --text-white: #ffffff;
    --card-shadow: 0 6px 18px rgba(40, 30, 20, 0.28);
  }
  * { margin: 0; padding: 0; box-sizing: border-box; }
  html, body {
    width: 1200px;
    height: 1000px;
    overflow: hidden;
  }
  body {
    background: var(--backdrop);
    font-family: "Open Sans", Arial, sans-serif;
    position: relative;
  }
  .card {
    position: absolute;
    left: 265px;
    width: 666px;
    height: 397px;
    box-shadow: var(--card-shadow);
  }
  .card-front { top: 73px; background: var(--card-blue); color: var(--text-white); }
  .card-back { top: 533px; background: var(--card-charcoal); }

  .wordmark {
    position: absolute;
    font-weight: 600;
    line-height: 1;
    text-transform: uppercase;
  }
  .wordmark-name { display: block; letter-spacing: 0.01em; }
  .wordmark-tag { display: block; letter-spacing: 0.36em; }

  .card-front .wordmark {
    right: 33px;
    top: 60px;
    text-align: right;
    color: var(--text-white);
  }
  .card-front .wordmark-name { font-size: 40px; }
  .card-front .wordmark-tag { font-size: 17px; margin-top: 8px; margin-right: -6px; }

  .card-back .wordmark {
    left: 0;
    right: 0;
    top: 156px;
    text-align: center;
    color: var(--uv-charcoal);
  }
  .card-back .wordmark-name { font-size: 52px; }
  .card-back .wordmark-tag { font-size: 22px; margin-top: 10px; letter-spacing: 0.5em; margin-right: -0.5em; }

  .contact-block {
    position: absolute;
    left: 33px;
    top: 175px;
    font-size: 16px;
    line-height: 23px;
  }
  .person-name { font-size: 19px; font-weight: 600; line-height: 24px; }
  .person-title { font-size: 16px; }
  .contact-list { list-style: none; margin-top: 16px; }
  .contact-list li { display: flex; align-items: center; gap: 6px; }
  .contact-list svg { width: 16px; height: 16px; flex: none; fill: var(--text-white); }
  .postal-lines { margin-top: 7px; line-height: 26px; }
</style>
</head>
<body>
  <section class="card card-front" aria-label="Business card front">
    <div class="wordmark">
      <span class="wordmark-name">Brambleford</span>
      <span class="wordmark-tag">Constructions</span>
    </div>
    <div class="contact-block">
      <p class="person-name">GARETH PENNICK</p>
      <p class="person-title">Project Manager</p>
      <ul class="contact-list">
        <li>
          <svg viewBox="0 0 16 16" aria-hidden="true"><path d="M5 1h6a1 1 0 0 1 1 1v12a1 1 0 0 1-1 1H5a1 1 0 0 1-1-1V2a1 1 0 0 1 1-1zm.4 1.4v9.6h5.2V2.4zM8 12.8a.8.8 0 1 0 0 1.6.8.8 0 0 0 0-1.6z"/></svg>
          <span>0427 351 804</span>
        </li>
        <li>
          <svg viewBox="0 0 16 16" aria-hidden="true"><path d="M1 6c0-2 3-3 7-3s7 1 7 3v1.2h-3.4V5.6c-1-.4-2.3-.5-3.6-.5s-2.6.1-3.6.5v1.6H1zm3.6 1.6h6.8l2.4 5.4H2.2zM8 8.8a1.8 1.8 0 1 0 0 3.6 1.8 1.8 0 0 0 0-3.6z"/></svg>
          <span>(08) 9316 5172</span>
        </li>
        <li>
          <svg viewBox="0 0 16 16" aria-hidden="true"><path d="M1.5 4h13v8.5h-13zM2.3 4.6 8 9l5.7-4.4v.9L8 10 2.3 5.5z"/></svg>
          <span>info@bramblefordhomes.com.au</span>
        </li>
      </ul>
      <p class="postal-lines">PO Box 3817 Malaga WA 6944<br>47C Corvell Street, Malaga WA 6090</p>
    </div>
  </section>

  <section class="card card-back" aria-label="Business card back">
    <div class="wordmark">
      <span class="wordmark-name">Brambleford</span>
      <span class="wordmark-tag">Constructions</span>
    </div>
  </section>
</body>
</html>
```